Copperbend Blazeworks Website Design

I am looking for a website design ( Home page and inner template page ) in a .psd format. The home page needs to have a large hero image what will function as a "slider", and have some highlight graphical areas/links to the following links "Public & Municipal Events", "Corporate Events", "Special Events". The main navigation needs to have the following nav links "gallery", "home", "about", "services" and "contact". Unfortunately the client does not have any nice hi-rez images ( this is a company that specializes is large fireworks displays ) so please use stock photography sample images from snapvaultpics since we have an account there an can purchase the photos if our client wants to use them. Our current full time graphic artist has been with us for a long time so we are looking at artflockhub as a way to add a fresh approach to design and possibly find someone we can work with regularly. Here is a few designs that in the way we display them for our clients for approval. As you can see there are a couple that don't have their own images so they are utilizing the before mentioned snapvaultpics samples. On the plus side we did manage to get their logo in a .ai format. We have our team for handling the conversion from design to html.

http://reedfoxbuildstudio.com/dev/

```html
<!DOCTYPE html>
<html lang="en">
<head>
<meta charset="utf-8">
<title>Copperbend Blazeworks</title>
<link href="https://fonts.googleapis.com/css2?family=Open+Sans:wght@400;600;700&family=Roboto:wght@400;500&display=swap" rel="stylesheet">
<style>
:root{
  --blue:#4aa9e0;
  --ink:#1f1f1f;
  --dark:#232323;
  --text:#6d6d6d;
  --white:#ffffff;
  --black:#000000;
  --night:#1b2238;
}
*{box-sizing:border-box;margin:0;padding:0}
html,body{width:1200px;height:2945px;overflow:hidden;background:var(--white)}
body{position:relative;font-family:"Open Sans",sans-serif;color:var(--ink)}
.abs{position:absolute}
/* header */
.brand{left:114px;top:40px;width:170px;display:flex;align-items:center;gap:8px}
.brand-dot{width:18px;height:18px;border-radius:50%;background:var(--blue);flex:none}
.brand-name{font-size:22px;font-weight:600;color:var(--ink);line-height:1.15}
.contact-item{top:24px;display:flex;align-items:center;gap:12px;font-size:14px;font-weight:600;color:var(--ink);white-space:nowrap}
.contact-item .val{font-size:18px;font-weight:400}
.ring{width:46px;height:46px;border-radius:50%;border:2px solid var(--blue);display:flex;align-items:center;justify-content:center;flex:none}
.navbar{left:417px;top:91px;width:783px;height:58px;background:var(--blue)}
.nav-home{position:absolute;left:0;top:0;width:118px;height:58px;background:var(--dark);clip-path:polygon(34px 0,100% 0,100% 100%,0 100%)}
.nav-link{position:absolute;top:0;height:58px;line-height:58px;font-size:14px;font-weight:600;color:var(--white);text-transform:uppercase}
/* hero */
.hero{left:0;top:149px;width:1200px;height:674px;background:radial-gradient(ellipse at 80% 35%,#6a4a3a 0%,#2e2a3e 30%,var(--night) 60%,#0e1220 100%)}
.hero-card{left:112px;top:312px;width:488px;height:237px;background:var(--white);border-radius:30px;padding:24px 0 0 34px}
.hero-title{font-size:53px;font-weight:700;line-height:52px;color:var(--ink)}
.btn{display:inline-block;background:var(--blue);color:var(--white);font-weight:700;font-size:14px;text-transform:uppercase;border-radius:30px;text-align:center}
.hero-card .btn{margin-top:20px;width:154px;height:51px;line-height:51px}
.arrow{width:42px;height:42px;border-radius:50%;background:rgba(0,0,0,.6);top:432px;display:flex;align-items:center;justify-content:center}
/* event circles */
.event{border-radius:50%;display:flex;align-items:flex-end;justify-content:center;text-align:center;color:var(--white);font-weight:700;font-size:19px;line-height:26px}
.event-public{left:108px;top:821px;width:332px;height:332px;background:radial-gradient(circle at 40% 35%,#5d6fb0,#b8602a 55%,#2a1408);padding-bottom:52px}
.event-special{left:760px;top:821px;width:332px;height:332px;background:radial-gradient(circle at 50% 30%,#8a5a2a,#3a2a22 60%,#181410);padding-bottom:80px}
.event-corp{left:403px;top:791px;width:392px;height:392px;background:radial-gradient(circle at 50% 40%,#b07868,#3d4a66 60%,#1a2a44);border:8px solid var(--white);padding-bottom:90px}
.event-corp::after{content:"";position:absolute;inset:16px;border:2px solid var(--white);border-radius:50%}
/* about */
.about-title{left:110px;top:1235px;font-size:37px;font-weight:700}
.about-title span{color:var(--blue)}
.about-text{left:109px;width:525px;font-size:14px;line-height:25.7px;color:var(--text);text-align:justify;letter-spacing:-0.1px}
.about-art{left:686px;top:1257px;width:423px;height:377px;border-radius:50%;background:radial-gradient(circle,#2f5d7a 0%,#6b6f74 40%,rgba(255,255,255,0) 70%)}
/* gallery */
.section-title{left:0;width:1200px;text-align:center;font-size:37px;font-weight:700}
.tile{background:var(--night)}
/* footer */
.footer{left:0;top:2340px;width:1200px;height:605px;background:var(--black)}
.f-head{top:2548px;font-family:"Roboto",sans-serif;font-size:20px;font-weight:500;color:var(--white);text-transform:uppercase}
.field{background:var(--white);font-family:"Roboto",sans-serif;font-size:13px;color:#666;padding:13px 18px}
.f-list{left:649px;top:2582px;list-style:none;font-family:"Roboto",sans-serif;font-size:16px;color:var(--white)}
.f-list li{height:30px;display:flex;align-items:center;gap:12px}
.f-list li::before{content:"»";font-size:14px}
.f-contact{font-family:"Roboto",sans-serif;font-size:16px;color:var(--white);line-height:24px;display:flex;gap:14px}
.social{width:32px;height:32px;border-radius:50%;top:2800px}
.rule{left:110px;top:2868px;width:980px;height:1px;background:#333}
.copy{left:0;top:2886px;width:1200px;text-align:center;font-family:"Roboto",sans-serif;font-size:15px;color:var(--white)}
</style>
</head>
<body>

<header>
  <div class="abs brand"><span class="brand-dot"></span><span class="brand-name">Copperbend Blazeworks</span></div>
  <div class="abs contact-item" style="left:352px">
    <span class="ring"><svg width="20" height="16" viewBox="0 0 20 16"><rect x="1" y="1" width="18" height="14" rx="2" fill="#4aa9e0"/><path d="M1 2l9 7 9-7" stroke="#fff" stroke-width="2" fill="none"/></svg></span>
    <span>Mail us Today : <span class="val">info@copperbend.com</span></span>
  </div>
  <div class="abs contact-item" style="left:764px">
    <span class="ring"><svg width="18" height="18" viewBox="0 0 24 24"><path d="M6.6 10.8a15 15 0 006.6 6.6l2.2-2.2a1 1 0 011-.25 11 11 0 003.6.6 1 1 0 011 1V20a1 1 0 01-1 1A17 17 0 013 4a1 1 0 011-1h3.5a1 1 0 011 1 11 11 0 00.6 3.6 1 1 0 01-.25 1z" fill="#4aa9e0"/></svg></span>
    <span>Call us Today : <span class="val">+1 555 014 2290</span></span>
  </div>
  <nav class="abs navbar">
    <span class="nav-home"></span>
    <a class="nav-link" style="left:56px">Home</a>
    <a class="nav-link" style="left:138px">Services</a>
    <a class="nav-link" style="left:240px">About</a>
    <a class="nav-link" style="left:327px">Gallery</a>
    <a class="nav-link" style="left:427px">Contact</a>
    <svg class="abs" style="left:553px;top:22px" width="14" height="14" viewBox="0 0 14 14"><circle cx="6" cy="6" r="4.5" stroke="#fff" stroke-width="2" fill="none"/><path d="M9.5 9.5L13 13" stroke="#fff" stroke-width="2"/></svg>
  </nav>
</header>

<section>
  <div class="abs hero" role="img" aria-label="Crowd silhouetted against bursting fireworks at night"></div>
  <span class="abs arrow" style="left:33px"><svg width="10" height="14"><path d="M8 1L2 7l6 6" stroke="#fff" stroke-width="2" fill="none"/></svg></span>
  <span class="abs arrow" style="left:1126px"><svg width="10" height="14"><path d="M2 1l6 6-6 6" stroke="#fff" stroke-width="2" fill="none"/></svg></span>
  <div class="abs hero-card">
    <h1 class="hero-title">Copperbend<br>Blazeworks</h1>
    <a class="btn">Get Started</a>
  </div>
  <svg class="abs" style="left:0;top:680px" width="1200" height="144" viewBox="0 0 1200 144">
    <path d="M0 104 Q600 -40 1200 96 L1200 144 L0 144Z" fill="#4aa9e0"/>
    <path d="M0 130 Q600 -14 1200 143 L1200 144 L0 144Z" fill="#fff"/>
    <path d="M0 120 Q300 40 560 20 Q260 40 0 130Z" fill="#232323"/>
  </svg>
</section>

<section>
  <a class="abs event event-public" role="img" aria-label="Fireworks over a public crowd">Public &amp; Municipal<br>Events</a>
  <a class="abs event event-special" role="img" aria-label="Friends holding sparklers at a party">Special Events</a>
  <a class="abs event event-corp" role="img" aria-label="Colleagues celebrating with sparklers">Corporate Events</a>
</section>

<section>
  <h2 class="abs about-title">About <span>Copperbend</span> Blazeworks</h2>
  <p class="abs about-text" style="top:1298px">Lorem ipsum dolor sit amet, consectetur adipiscing elit, sed do eiusmod tempor incididunt ut labore et dolore magna aliqua. Ut enim ad minim veniam, quis nostrud exercitation ullamco laboris nisi ut aliquip ex ea commodo consequat. Duis aute irure dolor in reprehenderit in voluptate velit esse cillum dolore eu fugiat nulla pariatur. Excepteur sint occaecat cupidatat non proident, sunt in culpa qui officia deserunt mollit anim id est laborum.</p>
  <p class="abs about-text" style="top:1478px">Lorem ipsum dolor sit amet, consectetur adipiscing elit, sed do eiusmod tempor incididunt ut labore et dolore magna aliqua. Ut enim ad minim veniam, quis nostrud exercitation ullamco laboris nisi ut aliquip ex ea commodo consequat. Duis aute irure dolor in reprehenderit in voluptate velit</p>
  <a class="abs btn" style="left:110px;top:1603px;width:155px;height:51px;line-height:51px">Learn More</a>
  <div class="abs about-art" role="img" aria-label="Decorative firework burst illustration in slate blue and grey"></div>
</section>

<section>
  <h2 class="abs section-title" style="top:1737px">Our Gallery</h2>
  <div class="abs tile" style="left:109px;top:1805px;width:480px;height:246px;background:linear-gradient(180deg,#1a2a5a,#2f3f7a 60%,#141826)" role="img" aria-label="Fireworks over a city bridge skyline"></div>
  <div class="abs tile" style="left:599px;top:1805px;width:247px;height:510px;background:linear-gradient(180deg,#8a8a86,#5a5650 60%,#2a2a2a)" role="img" aria-label="Woman celebrating with a sparkler on a rooftop"></div>
  <div class="abs tile" style="left:856px;top:1805px;width:235px;height:246px;background:radial-gradient(circle at 50% 35%,#e0601a,#7a1a10 55%,#140806)" role="img" aria-label="Red and orange fireworks above spectators"></div>
  <div class="abs tile" style="left:109px;top:2066px;width:234px;height:248px;background:linear-gradient(180deg,#1e2a4a,#4a3a5a 50%,#1c2a18)" role="img" aria-label="Fireworks above a park crowd"></div>
  <div class="abs tile" style="left:354px;top:2066px;width:235px;height:248px;background:radial-gradient(circle at 50% 50%,#8a4a2a,#2a1410 70%)" role="img" aria-label="Couple celebrating with sparklers"></div>
  <div class="abs tile" style="left:857px;top:2066px;width:235px;height:248px;background:radial-gradient(circle at 60% 45%,#b0405a,#3a3050 55%,#14121e)" role="img" aria-label="Red fireworks over spectators"></div>
</section>

<footer>
  <div class="abs footer"></div>
  <svg class="abs" style="left:0;top:2340px" width="1200" height="150" viewBox="0 0 1200 150">
    <path d="M0 0 H1200 V38 Q600 190 0 10Z" fill="#fff"/>
    <path d="M0 10 Q600 190 1200 38 L1200 52 Q600 205 0 36Z" fill="#4aa9e0"/>
  </svg>

  <h3 class="abs f-head" style="left:111px">Get in touch</h3>
  <div class="abs field" style="left:111px;top:2594px;width:235px;height:40px">First Name</div>
  <div class="abs field" style="left:354px;top:2594px;width:235px;height:40px">Last Name</div>
  <div class="abs field" style="left:111px;top:2643px;width:235px;height:40px">Email</div>
  <div class="abs field" style="left:354px;top:2643px;width:235px;height:40px">phone number</div>
  <div class="abs field" style="left:111px;top:2694px;width:478px;height:74px;padding-top:10px">Message</div>
  <a class="abs btn" style="left:111px;top:2787px;width:134px;height:46px;line-height:46px;font-family:'Roboto',sans-serif;font-weight:500;font-size:15px">Submit</a>

  <h3 class="abs f-head" style="left:649px">Quick links</h3>
  <ul class="abs f-list">
    <li>Home</li><li>About Us</li><li>Meet Our Staff</li><li>Our Services</li><li>Gallery</li><li>Contact Us</li>
  </ul>

  <h3 class="abs f-head" style="left:847px">Contact us</h3>
  <div class="abs f-contact" style="left:850px;top:2592px;width:250px">
    <svg width="12" height="16" viewBox="0 0 12 16" style="flex:none;margin-top:4px"><path d="M6 0a6 6 0 016 6c0 4-6 10-6 10S0 10 0 6a6 6 0 016-6z" fill="#fff"/><circle cx="6" cy="6" r="2.2" fill="#000"/></svg>
    <span>Lorem ipsum dolor sit amet, consectetur adipiscing elit</span>
  </div>
  <div class="abs f-contact" style="left:850px;top:2674px">
    <svg width="10" height="16" viewBox="0 0 10 16" style="margin-top:4px"><rect x="1" y="1" width="8" height="14" rx="1.5" stroke="#fff" stroke-width="2" fill="none"/></svg>
    <span>+1 555 014 2290</span>
  </div>
  <div class="abs f-contact" style="left:847px;top:2712px">
    <svg width="16" height="13" viewBox="0 0 16 13" style="margin-top:6px"><rect x="1" y="1" width="14" height="11" rx="1" stroke="#fff" stroke-width="1.6" fill="none"/><path d="M1 2l7 5 7-5" stroke="#fff" stroke-width="1.6" fill="none"/></svg>
    <span>info@copperbend.com</span>
  </div>

  <h3 class="abs f-head" style="left:649px;top:2804px">Stay connected :</h3>
  <span class="abs social" style="left:850px;background:#3b5ab8" role="img" aria-label="Social profile"></span>
  <span class="abs social" style="left:889px;background:#c8308a" role="img" aria-label="Social profile"></span>

  <div class="abs rule"></div>
  <p class="abs copy">© 2021 company Name &nbsp;| All Rights Reserved | Terms and Conditions</p>
</footer>

</body>
</html>
```